Velutra Showcases | Web Design Project

We need a web design for a new Promotion Company based in Toronto, Canada named Velutra Showcases.

Velutra Showcases has an idea and vision to set high standard, be EXCLUSIVE and attract a group of people that will follow us through events we promote (night clubs, brand promotions, music events, and sport events)

We want to present a high standards and classy image to the others...

layout/style of the website would be best explained by this template

http://www.gorvikdesigns.example/view-ttemplate-58174.html

Target Market(s)

male/female age 25-40 Target: business owners young entrepreneur - clubing industry - media industry - promotion industry - marketing media industry

Industry/Entity Type

It Company

Requirements
Must have
• website would have about 5 pages ... example in terms of content (http://www.brastonhouse.example/lifestyle.html)

About Velutra
Events
Media
Promotions
Affiliates
Contact

as well as twitter and facebook logo/links
newsletter section
music control

need to have a easy to view gallery page (pictures from events)
Events would have to include flyers .. for past/future events
Media - would include videos/pictures from the events

Affiliates - list of affiliates with their logos and short description..

Main Pages
background would be pictures of Toronto
it would be nice to have some kind of flash/swf
space for flyer and picture of the week...

logo file is uploaded.

```html
<!DOCTYPE html>
<html lang="en">
<head>
<meta charset="utf-8">
<title>Velutra Showcases – About</title>
<link rel="stylesheet" href="https://fonts.googleapis.com/css2?family=Jost:wght@400&family=Source+Sans+3:wght@400;500&display=swap">
<style>
  :root {
    --bar: #000000;
    --panel: rgba(8, 7, 6, 0.82);
    --accent: #2fa7e0;
    --text: #ffffff;
    --muted: #d9d9d9;
    --sepia-light: #8a7350;
    --sepia-mid: #4a3d2a;
    --sepia-dark: #15110b;
    --scroll-track: #6a6a6a;
    --scroll-thumb: #7d7d7d;
  }
  * { margin: 0; padding: 0; box-sizing: border-box; }
  html, body { width: 1200px; height: 750px; overflow: hidden; }
  body {
    position: relative;
    background: var(--sepia-dark);
    font-family: "Source Sans 3", "Myriad Pro", sans-serif;
    color: var(--text);
  }
  .city-backdrop {
    position: absolute; inset: 0;
    background:
      radial-gradient(ellipse 70% 45% at 50% 30%, var(--sepia-light) 0%, transparent 70%),
      linear-gradient(180deg, #5e4e36 0%, var(--sepia-mid) 35%, #1d170f 62%, #2a2318 80%, #0e0b07 100%);
  }
  .top-bar {
    position: absolute; top: 0; left: 0; width: 1200px; height: 28px;
    background: var(--bar);
  }
  .home-link { position: absolute; left: 17px; top: 6px; width: 17px; height: 16px; }
  .main-nav a {
    position: absolute; top: 3px;
    font-family: "Jost", "Futura", sans-serif; font-size: 18px; line-height: 22px;
    color: var(--text); text-decoration: none; text-transform: uppercase; white-space: nowrap;
  }
  .main-nav a.is-current { color: var(--accent); }
  .player { position: absolute; left: 913px; top: 9px; height: 11px; }
  .now-playing {
    position: absolute; left: 1003px; top: 7px;
    font-size: 11px; line-height: 14px; color: var(--text); white-space: nowrap;
  }
  .content-panel {
    position: absolute; left: 226px; top: 47px; width: 749px; height: 655px;
    background: var(--panel);
  }
  .brand {
    position: absolute; left: 0; top: 82px; width: 1200px; text-align: center;
    font-family: "Jost", "Futura", sans-serif; font-size: 38px; line-height: 44px;
    letter-spacing: 4px; color: var(--accent); text-transform: uppercase;
  }
  .gallery {
    position: absolute; left: 272px; top: 180px; width: 656px; height: 250px;
    background: #000;
  }
  .gallery .shot { position: absolute; }
  .shot-stage { left: 0; top: 0; width: 220px; height: 90px; background: linear-gradient(180deg, #8a8aa0, #3b3f55 60%, #2a2a2a); }
  .shot-crowd { left: 221px; top: 0; width: 211px; height: 90px; background: linear-gradient(160deg, #3a2a6a, #b06aa0 50%, #2f3a5a); }
  .shot-dj { left: 433px; top: 0; width: 223px; height: 240px; background: radial-gradient(ellipse at 40% 15%, #fff6d0, #b8923a 35%, #3a2a14 70%, #120c06); }
  .shot-flyer { left: 15px; top: 102px; width: 187px; height: 137px; background: linear-gradient(135deg, #f0a020, #e85a30 50%, #d0308a); }
  .shot-lights { left: 221px; top: 90px; width: 211px; height: 150px; background: linear-gradient(160deg, #6a3aa0, #c05ac0 40%, #20204a 75%, #050505); }
  .scrollbar-track { position: absolute; left: 960px; top: 180px; width: 2px; height: 497px; background: var(--scroll-track); }
  .scrollbar-thumb { position: absolute; left: 954px; top: 212px; width: 16px; height: 50px; background: var(--scroll-thumb); }
  .about-copy {
    position: absolute; left: 272px; width: 657px;
    font-size: 12.6px; font-weight: 500; line-height: 15.4px; color: var(--text);
  }
  .about-copy span { display: block; white-space: nowrap; }
  .copy-one { top: 450px; } .copy-two { top: 537px; } .copy-three { top: 617px; }
  .site-footer {
    position: absolute; left: 0; top: 722px; width: 1200px; height: 28px; background: var(--bar);
  }
  .legal {
    position: absolute; left: 8px; top: 6px;
    font-family: "Jost", "Futura", sans-serif; font-size: 13px; line-height: 16px;
    text-transform: uppercase; color: var(--muted); white-space: nowrap;
  }
  .legal a { color: var(--accent); text-decoration: none; }
  .social { position: absolute; top: 8px; width: 14px; height: 14px; }
  .social-feed { left: 1126px; background: #e8832a; }
  .social-micro { left: 1151px; background: #6fb8d8; }
  .social-friends { left: 1175px; background: #3b5b9a; }
</style>
</head>
<body>
  <div class="city-backdrop" role="img" aria-label="Sepia photo of the Toronto skyline across the water at dusk, framed by trees"></div>

  <header class="top-bar">
    <svg class="home-link" viewBox="0 0 17 16" aria-label="Home"><path d="M8.5 0 L17 8 H14.5 V16 H10.5 V11 H6.5 V16 H2.5 V8 H0 Z" fill="#fff"/></svg>
    <nav class="main-nav">
      <a class="is-current" href="#" style="left:51px">About Velutra</a>
      <a href="#" style="left:237px">Media</a>
      <a href="#" style="left:332px">Events</a>
      <a href="#" style="left:426px">Promotions</a>
      <a href="#" style="left:560px">Affiliates</a>
      <a href="#" style="left:680px">Contact</a>
    </nav>
    <svg class="player" width="75" height="11" viewBox="0 0 75 11" aria-label="Music controls">
      <rect x="0" y="0" width="2" height="10" fill="#fff"/><path d="M8 0 L2 5 L8 10 Z" fill="#fff"/>
      <path d="M23 0 L30 5 L23 10 Z" fill="#fff"/>
      <path d="M41 0 L48 5 L41 10 Z" fill="#fff"/><rect x="48" y="0" width="2" height="10" fill="#fff"/>
      <rect x="63" y="0" width="10" height="10" fill="#fff"/>
    </svg>
    <div class="now-playing">Mira Solen; Velvet Hours (Radio Edit).....</div>
  </header>

  <main class="content-panel"></main>
  <div class="brand">Velutra Showcases</div>

  <section class="gallery">
    <div class="shot shot-stage" role="img" aria-label="Open-air festival main stage under an evening sky"></div>
    <div class="shot shot-crowd" role="img" aria-label="Crowd with raised hands under coloured festival lights"></div>
    <div class="shot shot-dj" role="img" aria-label="DJ on stage facing a large crowd under bright spotlights"></div>
    <div class="shot shot-flyer" role="img" aria-label="Colourful flyer for a summer dance festival weekend"></div>
    <div class="shot shot-lights" role="img" aria-label="Dancing crowd silhouetted against laser lights and a banner"></div>
  </section>

  <div class="scrollbar-track"></div>
  <div class="scrollbar-thumb"></div>

  <p class="about-copy copy-one">
    <span>Lorem ipsum dolor sit amet, consetetur sadipscing elitr, sed diam nonumy eirmod tempor invidunt ut labore et dolore</span>
    <span>erat, sed diam voluptua. At vero eos et accusam et justo duo dolores et ea rebum. Stet clita kasd gubergren, no sea</span>
    <span>Lorem ipsum dolor sit amet. Lorem ipsum dolor sit amet, consetetur sadipscing elitr,&nbsp; sed diam nonumy eirmod tempor</span>
    <span>et dolore magna aliquyam erat, sed diam voluptua. At vero eos et accusam et justo duo dolores et ea</span>
  </p>
  <p class="about-copy copy-two">
    <span>Lorem ipsum dolor sit amet, consetetur sadipscing elitr, sed diam nonumy eirmod tempor invidunt ut labore et dolore</span>
    <span>erat, sed diam voluptua. At vero eos et accusam et justo duo dolores et ea rebum. Stet clita kasd gubergren, no sea</span>
    <span>Lorem ipsum dolor sit amet. Lorem ipsum dolor sit amet, consetetur sadipscing elitr,&nbsp; sed diam nonumy eirmod tempor</span>
    <span>et dolore magna aliquyam erat, sed diam voluptua. At vero eos et accusam et justo duo dolores et ea</span>
  </p>
  <p class="about-copy copy-three">
    <span>Lorem ipsum dolor sit amet, consetetur sadipscing elitr, sed diam nonumy eirmod tempor invidunt ut labore et dolore</span>
    <span>erat, sed diam voluptua. At vero eos et accusam et justo duo dolores et ea rebum. Stet clita kasd gubergren, no sea</span>
    <span>Lorem ipsum dolor sit amet. Lorem ipsum dolor sit amet, consetetur sadipscing elitr,&nbsp; sed diam nonumy eirmod tempor</span>
    <span>et dolore magna aliquyam erat, sed diam voluptua. At vero eos et accusam et justo duo dolores et ea</span>
  </p>

  <footer class="site-footer">
    <div class="legal">Copyright © 2011 Velutra. Use of this website constitutes acceptance of our <a href="#">User Agreement</a> and <a href="#">Privacy Policy</a>.</div>
    <a class="social social-feed" href="#" aria-label="News feed"></a>
    <a class="social social-micro" href="#" aria-label="Microblog"></a>
    <a class="social social-friends" href="#" aria-label="Social network"></a>
  </footer>
</body>
</html>
```